Indy Film Production Company/Studio

We need a business card designed from an existing logo. We are a digital studio/production company that caters to creating genre entertainment, like Action, Horror, and martial arts. The card along with the logo will be used to Brand the company from letter heads to banners. The design will also be used for postcards and Brochures. It should be professional and masculine.
Updates

Thank you to all the designers who have participated. I'm narrowing down who it will be. Thank you again.

Target Market(s)

Investors, Networks, Producers, and actors

Industry/Entity Type

Film Production

Contact Information for Business Card

Teodoro Valbuena
Producer/Writer/Director
www.kestrelpicturehouse.example

Requirements
Must have
• Website address, Facebook icon and Twitter icon possibly in the back of the card.
Nice to have
• Logline of Company: Follow The Action.

```html
<!DOCTYPE html>
<html lang="en">
<head>
<meta charset="utf-8">
<title>Kestrel Picture House – Business Card</title>
<link href="https://fonts.googleapis.com/css2?family=Roboto:wght@400;700;900&display=swap" rel="stylesheet">
<style>
  :root {
    --stage: #e6e6e6;
    --brand-red: #d9212b;
    --panel-red: #e3232d;
    --panel-red-dark: #c8141e;
    --card-white: #ffffff;
    --edge-grey: #dcdcdc;
    --charcoal: #2b2b2b;
    --charcoal-light: #363636;
    --muted: #a8a8a8;
    --ink-light: #ffffff;
  }
  * { box-sizing: border-box; margin: 0; padding: 0; }
  html, body { width: 1200px; height: 950px; overflow: hidden; }
  body {
    background: var(--stage);
    font-family: "Roboto", Arial, sans-serif;
    display: flex;
    flex-direction: column;
    align-items: center;
    justify-content: center;
    gap: 40px;
  }
  .card {
    width: 700px;
    height: 400px;
    position: relative;
    overflow: hidden;
    box-shadow: 0 10px 30px rgba(0,0,0,0.18);
  }

  /* Front */
  .card-front { background: var(--card-white); display: flex; }
  .front-brand {
    width: 46%;
    display: flex;
    align-items: center;
    justify-content: center;
    padding-left: 20px;
  }
  .brand-name {
    color: var(--brand-red);
    font-weight: 900;
    text-transform: uppercase;
    line-height: 0.95;
    letter-spacing: 1px;
  }
  .front-brand .brand-name { font-size: 40px; }
  .front-panel {
    width: 47%;
    background: linear-gradient(160deg, var(--panel-red) 0%, var(--panel-red-dark) 100%);
    color: var(--ink-light);
    display: flex;
    flex-direction: column;
    justify-content: center;
    padding: 0 24px 0 40px;
  }
  .front-edge { width: 7%; background: var(--edge-grey); }
  .person-name {
    font-weight: 700;
    font-size: 21px;
    letter-spacing: 1px;
    text-transform: uppercase;
  }
  .person-role {
    font-size: 15px;
    letter-spacing: 0.8px;
    text-transform: uppercase;
    margin-top: 6px;
    margin-bottom: 26px;
  }
  .contact-list { list-style: none; }
  .contact-item {
    display: flex;
    align-items: center;
    gap: 9px;
    font-size: 14px;
    margin-bottom: 8px;
    white-space: nowrap;
  }
  .contact-item svg { width: 14px; height: 14px; flex: none; fill: var(--ink-light); }

  /* Back */
  .card-back {
    background: linear-gradient(135deg, var(--charcoal-light) 0%, var(--charcoal) 100%);
    display: flex;
    flex-direction: column;
    align-items: center;
    justify-content: center;
    gap: 26px;
  }
  .card-back .brand-name { font-size: 52px; text-align: center; }
  .back-web { color: var(--muted); font-size: 17px; letter-spacing: 2px; }
  .social-marks {
    position: absolute;
    top: 22px;
    right: 24px;
    display: flex;
    gap: 5px;
  }
  .social-mark { width: 22px; height: 22px; background: #cfcfcf; border-radius: 2px; }
</style>
</head>
<body>

  <section class="card card-front" aria-label="Business card front">
    <div class="front-brand">
      <div class="brand-name">Kestrel<br>Picture House</div>
    </div>
    <div class="front-panel">
      <h1 class="person-name">Teodoro Valbuena</h1>
      <p class="person-role">Producer/Writer/Director</p>
      <ul class="contact-list">
        <li class="contact-item">
          <svg viewBox="0 0 24 24" aria-hidden="true"><path d="M6.6 10.8a15 15 0 0 0 6.6 6.6l2.2-2.2c.3-.3.7-.4 1-.2 1.1.4 2.3.6 3.6.6.6 0 1 .4 1 1V20c0 .6-.4 1-1 1A17 17 0 0 1 3 4c0-.6.4-1 1-1h3.5c.6 0 1 .4 1 1 0 1.3.2 2.5.6 3.6.1.3 0 .7-.2 1z"/></svg>
          555 0142 7788
        </li>
        <li class="contact-item">
          <svg viewBox="0 0 24 24" aria-hidden="true"><path d="M2 5h20v14H2z" fill="none"/><path d="M2 5h20v1.5l-10 6.5L2 6.5zM2 8.5l10 6.5 10-6.5V19H2z"/></svg>
          teodoro@kestrelpicturehouse.example
        </li>
        <li class="contact-item">
          <svg viewBox="0 0 24 24" aria-hidden="true"><circle cx="12" cy="12" r="10"/></svg>
          www.kestrelpicturehouse.example
        </li>
      </ul>
    </div>
    <div class="front-edge"></div>
  </section>

  <section class="card card-back" aria-label="Business card back">
    <div class="social-marks">
      <span class="social-mark"></span>
      <span class="social-mark"></span>
    </div>
    <div class="brand-name">Kestrel<br>Picture House</div>
    <p class="back-web">www.kestrelpicturehouse.example</p>
  </section>

</body>
</html>
```